Animal Eye Clinic needs a Business card

We are a new veterinary ophthalmology practice (Ridgeline Pet Vision Care) and we need a business card designed. We only see animal eyes - we are not a regular veterinary clinic. We already have a logo. We are looking for a professional, good looking business card to hand out to our clients. We are looking for something simple but professional and contemporary. Our logo is likely the only picture/graphic that needs to be on the card.
Updates

Contact Information for Business Card

Delia Vossman, BSc, DVM, MSc, DipACVO
Veterinary Ophthalmologist

Phone: 250.418.3927
Email: ridgelinepetvisioncare@mailbox-example.net
Website: ridgelinepetvisioncare-example.net
Address: 1874 Thornbury Rd
Kelowna, BC, V1X 4M9

Colors

Designer to choose colors to be used in the design.

Requirements
Must have
• Our logo (attached)

```html
<!DOCTYPE html>
<html lang="en">
<head>
<meta charset="utf-8">
<title>Ridgeline Pet Vision Care – Business Card</title>
<link href="https://fonts.googleapis.com/css2?family=Roboto:wght@400;500&display=swap" rel="stylesheet">
<style>
  :root {
    --backdrop: #c8c8c8;
    --teal: #0497a9;
    --teal-deep: #0a6f7d;
    --ink: #5f5f5f;
    --paper: #ffffff;
  }
  * { box-sizing: border-box; margin: 0; padding: 0; }
  html, body {
    width: 1200px; height: 794px; overflow: hidden;
    background: var(--backdrop);
    font-family: "Roboto", Arial, sans-serif;
  }
  .card {
    position: absolute; top: 267px;
    width: 455px; height: 261px;
    overflow: hidden;
    box-shadow: 0 2px 4px rgba(0,0,0,0.25);
  }
  .card--front { left: 141px; background: var(--paper); }
  .card--back { left: 601px; background: var(--teal); }

  .brand { position: absolute; left: 20px; top: 26px; display: flex; align-items: center; gap: 10px; }
  .brand__dot { width: 52px; height: 52px; border-radius: 50%; background: var(--teal); }
  .brand__name {
    color: var(--teal); font-weight: 500; font-size: 17px; line-height: 19px;
    text-transform: uppercase;
  }

  .person { position: absolute; left: 20px; top: 88px; }
  .person__name { color: var(--teal); font-weight: 500; font-size: 16px; letter-spacing: 0.2px; }
  .person__creds { color: var(--teal); font-size: 11.5px; margin-top: 3px; }
  .person__role { color: var(--ink); font-size: 12px; margin-top: 3px; }

  .address { position: absolute; left: 21px; top: 150px; color: var(--ink); font-size: 12px; line-height: 17px; font-style: normal; }

  .contact { position: absolute; left: 21px; top: 195px; list-style: none; color: var(--ink); font-size: 12px; line-height: 16.5px; }
  .contact li { display: flex; align-items: center; gap: 3px; }
  .contact svg { width: 9px; height: 9px; fill: var(--teal); flex: none; }

  .front-art {
    position: absolute; left: 330px; top: 18px;
    width: 246px; height: 246px; border-radius: 50%;
    background: radial-gradient(circle at 45% 55%, #15a4b5, var(--teal) 70%);
  }

  .back-art {
    position: absolute; left: 0; top: 0; width: 128px; height: 261px;
    background: linear-gradient(160deg, var(--teal-deep) 0%, #3aa9b8 65%, rgba(4,151,169,0) 100%);
    border-radius: 0 60px 60px 0;
    opacity: 0.85;
  }
  .back-brand {
    position: absolute; left: 169px; top: 172px;
    color: #ffffff; font-weight: 500; font-size: 24px; line-height: 26px;
    text-transform: uppercase;
  }
</style>
</head>
<body>
  <section class="card card--front">
    <div class="brand">
      <span class="brand__dot"></span>
      <span class="brand__name">Ridgeline<br>Pet Vision Care</span>
    </div>

    <div class="person">
      <p class="person__name">DELIA VOSSMAN</p>
      <p class="person__creds">BSc, DVM, MSc, DipACVO</p>
      <p class="person__role">Veterinary Ophthalmologist</p>
    </div>

    <address class="address">1874 Thornbury Rd<br>Kelowna, BC, V1X 4M9</address>

    <ul class="contact">
      <li><svg viewBox="0 0 10 10"><path d="M2 0.5 L3.8 2.6 L2.9 3.8 Q4 6 6.2 7.1 L7.4 6.2 L9.5 8 L8.4 9.5 Q1.5 8.5 0.5 1.6 Z"/></svg>250.418.3927</li>
      <li><svg viewBox="0 0 10 10"><path d="M0.5 2 H9.5 V8 H0.5 Z M0.5 2 L5 5.3 L9.5 2" stroke="#fff" stroke-width="0.8"/></svg>ridgelinepetvisioncare@mailbox-example.net</li>
      <li><svg viewBox="0 0 10 10"><circle cx="5" cy="5" r="4.5"/></svg>ridgelinepetvisioncare-example.net</li>
    </ul>

    <div class="front-art" role="img" aria-label="Illustration of a dog, horse and cat in a teal circle"></div>
  </section>

  <section class="card card--back">
    <div class="back-art" role="img" aria-label="Faint silhouettes of a horse and cat"></div>
    <p class="back-brand">Ridgeline<br>Pet Vision Care</p>
  </section>
</body>
</html>
```